Travel, Resort and Tourism Advisor

I am looking for a classy and slick website for a travel, resort and tourism website which will offer first hand advise to tourist and fun seekers on the best locations and remarkable places to relax and unwind. We are primary located in the United States but will offer services to people worldwide. My website will feature images and locations and analysis of the best resorts in the Industry. Designers can take an idea from http://wandervale.example It will include prices, safety tips, culture and how to make the best of your tourism. The website will compare different destinations and recommend places based on the user budget, culture, and ethnic nationality. I would want a colorful and attention seeking website. Have questions ask.
Industry/Entity Type
Tourism
Coding
Coded - Design and coding required
Number of Pages Required
1 page
Look and feel
Each slider illustrates characteristics of the customer's brand and the style your logo design should communicate.

```html
<!DOCTYPE html>
<html lang="en">
<head>
<meta charset="utf-8">
<title>Solvane – Travel, Resort and Tourism</title>
<link href="https://fonts.googleapis.com/css2?family=Open+Sans:wght@400;600;700&family=Raleway:wght@400;500;600&display=swap" rel="stylesheet">
<style>
:root{
  --orange:#f7941d;
  --teal:#1cb5a8;
  --teal-dark:#0d6f68;
  --ink:#333;
  --muted:#777;
  --light:#ececec;
  --white:#fff;
}
*{box-sizing:border-box;margin:0;padding:0}
html,body{width:1200px;height:2224px;overflow:hidden}
body{font-family:"Open Sans",Arial,sans-serif;color:var(--ink);background:var(--white);position:relative}
.abs{position:absolute}

/* header */
.site-header{left:0;top:0;width:1200px;height:84px;background:var(--white)}
.brand{left:140px;top:24px;display:flex;align-items:center;gap:10px;font-family:"Raleway",sans-serif;font-weight:600;font-size:30px;color:var(--ink)}
.brand .dot{width:14px;height:14px;border-radius:50%;background:var(--teal)}
.main-nav{right:140px;top:30px;display:flex;gap:34px;font-size:16px;font-weight:600;color:#555}
.main-nav .home{display:flex;align-items:center;gap:6px;color:var(--orange)}

/* hero */
.hero{left:0;top:84px;width:1200px;height:516px;background:linear-gradient(180deg,#6f8fae 0%,#c6a37a 45%,#e98f3a 62%,#3d4c57 100%)}
.hero-title{left:0;top:118px;width:1200px;text-align:center;font-family:"Raleway",sans-serif;font-size:54px;font-weight:500;color:var(--white)}
.hero-sub{left:0;top:182px;width:1200px;text-align:center;font-family:"Raleway",sans-serif;font-size:30px;color:var(--white)}
.search-bar{left:220px;top:230px;width:760px;height:56px;background:var(--teal);display:flex;align-items:center;gap:10px;padding:0 12px}
.search-bar .field{height:34px;background:var(--white);font-size:13px;color:#999;display:flex;align-items:center;padding:0 12px;justify-content:space-between}
.search-bar .location{width:320px}
.search-bar .date{width:140px}
.search-bar .submit{width:100px;height:34px;background:var(--teal-dark);color:var(--white);font-weight:700;font-size:14px;display:flex;align-items:center;justify-content:center}
.hero-arrow{top:290px}
.hero-dots{left:0;top:566px;width:1200px;display:flex;justify-content:center;gap:10px}
.hero-dots span{width:10px;height:10px;border-radius:50%;background:rgba(255,255,255,.6)}
.hero-dots span.on{background:var(--white)}

/* feature cards */
.feature{top:600px;width:290px;height:192px;display:flex;flex-direction:column;align-items:center;justify-content:center;gap:12px;color:var(--white);text-align:center}
.feature h3{font-family:"Raleway",sans-serif;font-size:22px;font-weight:600;line-height:1.15;padding:0 20px}
.feature .btn{background:var(--teal);font-size:12px;padding:6px 16px;font-weight:600}
.f1{left:140px;background:linear-gradient(160deg,#3d6ea1,#8bb4d4 50%,#5a7f4f)}
.f2{left:455px;background:linear-gradient(160deg,#d9c4ad,#b98d6b 55%,#7c5a43)}
.f3{left:770px;background:linear-gradient(160deg,#f5b233,#e9741b 60%,#c0561a)}
.f3 h3{color:#fff3c4}

/* popular */
.popular{left:0;top:832px;width:1200px;height:396px;background:var(--light)}
.section-title{font-family:"Raleway",sans-serif;font-size:30px;font-weight:500;color:#444}
.popular .section-title{left:140px;top:54px}
.slider-arrows{right:140px;top:62px;display:flex;gap:8px}
.slider-arrows span{width:26px;height:26px;background:var(--white);border:1px solid #ccc;display:flex;align-items:center;justify-content:center}
.dest{top:112px;width:220px;height:252px;background:var(--white)}
.dest .photo{height:196px}
.dest p{text-align:center;color:var(--orange);font-size:15px;font-weight:600;padding-top:16px}
.d1{left:140px}.d1 .photo{background:linear-gradient(180deg,#9fc6e4,#4f8a3e)}
.d2{left:370px}.d2 .photo{background:linear-gradient(180deg,#bcd6ea,#e8eef2 50%,#6f8a9a)}
.d3{left:600px}.d3 .photo{background:linear-gradient(180deg,#f2a24a,#c7502a 55%,#2b5f7d)}
.d4{left:830px;width:230px}.d4 .photo{background:linear-gradient(180deg,#5fbbe8,#8fd4e6 55%,#e8d7a8)}

/* testimonials */
.reviews{left:0;top:1262px;width:1200px;height:256px;background:linear-gradient(180deg,#4aa9dc,#8fd2ee 45%,#2bb0c2 70%,#9a7a54 100%);overflow:hidden}
.reviews .section-title{left:0;top:14px;width:1200px;text-align:center;color:var(--white);font-size:28px}
.quote-card{top:62px;width:268px;height:142px;background:var(--white);padding:16px 18px;box-shadow:0 2px 6px rgba(0,0,0,.15)}
.quote-card p{font-size:11px;line-height:1.45;color:var(--muted)}
.quote-card .author{display:flex;align-items:center;gap:10px;margin-top:12px}
.quote-card .avatar{width:34px;height:34px;border-radius:50%;background:linear-gradient(135deg,#b9a089,#6d5a4a)}
.quote-card .name{font-size:12px;font-weight:600;color:#555}
.quote-card .stars{color:var(--orange);font-size:12px;letter-spacing:1px}
.q0{left:-150px}.q1{left:176px}.q2{left:466px}.q3{left:756px}.q4{left:1082px}
.review-dots{left:0;top:222px;width:1200px;display:flex;justify-content:center;gap:8px}
.review-dots span{width:9px;height:9px;border-radius:50%;background:rgba(255,255,255,.6)}
.review-dots span.on{background:var(--white)}

/* spotlight & hotels */
.spotlight-title{left:140px;top:1560px}
.spot-photo{left:140px;top:1610px;width:200px;height:160px;background:linear-gradient(180deg,#7fc6ea,#2f8fb6 55%,#4d6b45)}
.spot-text{left:360px;top:1606px;width:240px}
.spot-text h4{color:var(--teal);font-size:15px;font-weight:600;line-height:1.3;margin-bottom:8px}
.spot-text p{font-size:11px;line-height:1.5;color:var(--muted)}
.spot-text .more{display:block;margin-top:10px;font-size:12px;font-weight:700;color:#444}
.hotels-title{left:640px;top:1560px}
.hotel{width:200px;display:flex;gap:14px}
.hotel .thumb{width:56px;height:56px;border-radius:50%;flex:none}
.hotel h5{font-size:12px;font-weight:700;color:var(--orange);margin-bottom:4px}
.hotel p{font-size:10.5px;line-height:1.4;color:var(--muted)}
.h1{left:640px;top:1612px}.h1 .thumb{background:linear-gradient(135deg,#e7a24f,#6d8fb0)}
.h2{left:860px;top:1612px}.h2 .thumb{background:linear-gradient(135deg,#7fb7d8,#c9d8e2)}
.h3{left:640px;top:1700px}.h3 .thumb{background:linear-gradient(135deg,#5b7f9a,#d5b58a)}
.h4{left:860px;top:1700px}.h4 .thumb{background:linear-gradient(135deg,#4b9fc9,#9bd0c4)}

/* footer */
.site-footer{left:0;top:1822px;width:1200px;height:402px;background:var(--orange)}
.foot-col{top:56px;color:var(--white)}
.foot-col h6{font-size:15px;font-weight:700;letter-spacing:.5px;margin-bottom:16px}
.foot-col li{list-style:none;font-size:13px;line-height:2;color:#fff4e3}
.c1{left:140px}.c2{left:380px}.c3{left:620px}.c4{left:860px}
.contact-line{display:flex;align-items:center;gap:8px;font-size:13px;line-height:2;color:#fff4e3}
.social{display:flex;gap:10px;margin-top:12px}
.social span{width:26px;height:26px;border-radius:50%;background:var(--white)}
.copyright{left:0;top:362px;width:1200px;text-align:center;font-size:12px;color:#fff4e3;border-top:1px solid rgba(255,255,255,.4);padding-top:12px}
</style>
</head>
<body>

<header class="site-header abs">
  <div class="brand abs"><span class="dot"></span>Solvane</div>
  <nav class="main-nav abs">
    <span class="home"><svg width="16" height="14" viewBox="0 0 16 14"><path d="M8 0L0 7h2v7h4V9h4v5h4V7h2z" fill="#f7941d"/></svg>Home</span>
    <span>About</span><span>Hotels</span><span>Flights</span><span>Tours</span><span>Book Now</span><span>Resources</span>
  </nav>
</header>

<section class="hero abs" role="img" aria-label="Resort terrace with pool and umbrellas at sunset over the sea"></section>
<h1 class="hero-title abs">Find Your Dream Tour with Us</h1>
<p class="hero-sub abs">Lorem nunc venenatis in tristique</p>
<form class="search-bar abs">
  <div class="field location">Location, City Name</div>
  <div class="field date">Check in <span>▾</span></div>
  <div class="field date">Check out <span>▾</span></div>
  <div class="submit">SEARCH</div>
</form>
<svg class="hero-arrow abs" style="left:128px" width="20" height="34" viewBox="0 0 20 34"><path d="M17 3L4 17l13 14" stroke="#fff" stroke-width="4" fill="none"/></svg>
<svg class="hero-arrow abs" style="left:1052px" width="20" height="34" viewBox="0 0 20 34"><path d="M3 3l13 14L3 31" stroke="#fff" stroke-width="4" fill="none"/></svg>
<div class="hero-dots abs"><span class="on"></span><span></span><span></span></div>

<article class="feature f1 abs" role="img" aria-label="Mountain lake destination"><h3>TRIP OF THE MONTH</h3><span class="btn">VIEW NOW</span></article>
<article class="feature f2 abs" role="img" aria-label="Traveller relaxing on a holiday stay"><h3>HOLIDAY STAYS</h3><span class="btn">VIEW NOW</span></article>
<article class="feature f3 abs" role="img" aria-label="Family tour special offer"><h3>SPECIAL OFFERS ON FAMILY TOURS</h3><span class="btn">VIEW NOW</span></article>

<section class="popular abs">
  <h2 class="section-title abs">Popular Destinations</h2>
  <div class="slider-arrows abs">
    <span><svg width="8" height="12" viewBox="0 0 8 12"><path d="M7 1L2 6l5 5" stroke="#888" stroke-width="2" fill="none"/></svg></span>
    <span><svg width="8" height="12" viewBox="0 0 8 12"><path d="M1 1l5 5-5 5" stroke="#888" stroke-width="2" fill="none"/></svg></span>
  </div>
  <div class="dest d1 abs"><div class="photo" role="img" aria-label="Alpine village in a green valley"></div><p>Class aptent taciti</p></div>
  <div class="dest d2 abs"><div class="photo" role="img" aria-label="Snowy mountain resort"></div><p>Class aptent taciti</p></div>
  <div class="dest d3 abs"><div class="photo" role="img" aria-label="Waterfront resort at sunset"></div><p>Class aptent taciti</p></div>
  <div class="dest d4 abs"><div class="photo" role="img" aria-label="Tropical beach with palm trees"></div><p>Class aptent taciti</p></div>
</section>

<section class="reviews abs" role="img" aria-label="Wooden jetty over turquoise sea">
  <h2 class="section-title abs">What People Say</h2>
  <div class="quote-card q0 abs"><p>“Lorem ipsum dolor sit amet consectetur adipiscing elit sed do eiusmod tempor incididunt ut labore.”</p></div>
  <div class="quote-card q1 abs"><p>“Lorem ipsum dolor sit amet consectetur adipiscing elit sed do eiusmod tempor incididunt ut labore et dolore magna.”</p><div class="author"><div class="avatar" role="img" aria-label="Reviewer portrait"></div><div><div class="name">By Author Name</div><div class="stars">★★★★★</div></div></div></div>
  <div class="quote-card q2 abs"><p>“Lorem ipsum dolor sit amet consectetur adipiscing elit sed do eiusmod tempor incididunt ut labore et dolore magna.”</p><div class="author"><div class="avatar" role="img" aria-label="Reviewer portrait"></div><div><div class="name">By Author Name</div><div class="stars">★★★★★</div></div></div></div>
  <div class="quote-card q3 abs"><p>“Lorem ipsum dolor sit amet consectetur adipiscing elit sed do eiusmod tempor incididunt ut labore et dolore magna.”</p><div class="author"><div class="avatar" role="img" aria-label="Reviewer portrait"></div><div><div class="name">By Author Name</div><div class="stars">★★★★★</div></div></div></div>
  <div class="quote-card q4 abs"><p>“Lorem ipsum dolor sit amet consectetur adipiscing elit sed do eiusmod tempor incididunt ut labore.”</p></div>
  <div class="review-dots abs"><span class="on"></span><span></span><span></span></div>
</section>

<h2 class="section-title spotlight-title abs">Spotlight Destination</h2>
<div class="spot-photo abs" role="img" aria-label="Overwater bungalows in a lagoon"></div>
<div class="spot-text abs">
  <h4>Praesent elementum elit at tellus nec ultrices vel porttitor.</h4>
  <p>Lorem ipsum dolor sit amet, consectetur adipiscing elit. Nulla facilisi vivamus luctus urna sed urna ultricies ac tempor dui sagittis. In condimentum facilisis porta sed nec diam eu diam mattis viverra.</p>
  <span class="more">READ MORE</span>
</div>

<h2 class="section-title hotels-title abs">Top Hotels</h2>
<div class="hotel h1 abs"><div class="thumb" role="img" aria-label="Hotel exterior"></div><div><h5>HOTEL NAME</h5><p>Lorem ipsum dolor sit amet elit sed do.</p></div></div>
<div class="hotel h2 abs"><div class="thumb" role="img" aria-label="Hotel exterior"></div><div><h5>HOTEL NAME</h5><p>Lorem ipsum dolor sit amet elit sed do.</p></div></div>
<div class="hotel h3 abs"><div class="thumb" role="img" aria-label="Hotel exterior"></div><div><h5>HOTEL NAME</h5><p>Lorem ipsum dolor sit amet elit sed do.</p></div></div>
<div class="hotel h4 abs"><div class="thumb" role="img" aria-label="Hotel exterior"></div><div><h5>HOTEL NAME</h5><p>Lorem ipsum dolor sit amet elit sed do.</p></div></div>

<footer class="site-footer abs">
  <div class="foot-col c1 abs"><h6>QUICK LINKS</h6><ul><li>About Us</li><li>Who We Are</li><li>Book Now</li><li>Blog Posts</li><li>Testimonials</li></ul></div>
  <div class="foot-col c2 abs"><h6>FIND YOUR TOUR</h6><ul><li>Luxury Resorts</li><li>Beach Escapes</li><li>Adventure Trips</li><li>Family Tours</li><li>Budget Stays</li></ul></div>
  <div class="foot-col c3 abs"><h6>RESOURCES</h6><ul><li>Support</li><li>FAQ</li><li>Safety Tips</li><li>Privacy Policy</li><li>Contact</li></ul></div>
  <div class="foot-col c4 abs"><h6>CONTACT US</h6>
    <div class="contact-line">240 Harbor View Drive, Suite 12</div>
    <div class="contact-line">Lakeside, CA 90210</div>
    <div class="contact-line"><svg width="14" height="14" viewBox="0 0 14 14"><path d="M3 1l2 3-1.5 1.5a7 7 0 0 0 5 5L10 9l3 2-1 2.5C6 13 1 8 .5 2z" fill="#fff"/></svg>(555) 014-2290</div>
    <div class="contact-line"><svg width="14" height="11" viewBox="0 0 14 11"><rect x="0.5" y="0.5" width="13" height="10" fill="none" stroke="#fff"/><path d="M1 1l6 5 6-5" stroke="#fff" fill="none"/></svg>hello@solvane.example</div>
    <div class="social"><span></span><span></span><span></span><span></span><span></span></div>
  </div>
  <div class="copyright abs">© 2024 Solvane. All rights reserved.</div>
</footer>

</body>
</html>
```